Haulage company, lets use ruby red white and some 3rd color for web design. and Garvel Pryce Transport logo

Target Market(s)

Transport industry

Industry/Entity Type

transport

Number of Pages Required

2 page

Requirements
Must have
• Logo

```html
<!DOCTYPE html>
<html lang="en">
<head>
<meta charset="utf-8">
<title>Garvel Pryce Transport</title>
<link href="https://fonts.googleapis.com/css2?family=Lexend:wght@300;400;500;600&family=Open+Sans:wght@600;700&display=swap" rel="stylesheet">
<style>
:root{
  --red:#e31e24;
  --red-dark:#8e0d10;
  --green:#2fb98a;
  --ink:#1f1f1f;
  --text:#4a4a4a;
  --muted:#8a8a8a;
  --soft:#f6f6f6;
  --white:#ffffff;
  --star:#f26522;
}
*{margin:0;padding:0;box-sizing:border-box}
html,body{width:1200px;height:4351px;overflow:hidden}
body{position:relative;font-family:"Lexend",sans-serif;color:var(--text);background:var(--white)}
.abs{position:absolute}
.brand{font-family:"Lexend",sans-serif;font-weight:500;color:var(--red);line-height:1.15;letter-spacing:0}
.btn{position:absolute;background:var(--red);color:var(--white);font-size:15px;font-weight:500;text-transform:uppercase;display:flex;align-items:center;justify-content:center;letter-spacing:.3px}
.section-title{position:absolute;font-size:32px;font-weight:500;color:var(--ink);text-transform:uppercase;letter-spacing:.3px}
.underline{position:absolute;height:3px;width:110px;background:var(--green)}
.photo{position:absolute}
.para{position:absolute;font-size:13.5px;line-height:25px;color:var(--text);font-weight:300}
.nav a{color:var(--white);text-decoration:none;font-size:15px;font-weight:500}
.arrows{position:absolute;display:flex;gap:20px}
.card-head{position:absolute;font-size:19px;font-weight:500;color:var(--green);text-transform:uppercase}
.faq{position:absolute;width:514px;height:54px;background:var(--white);border:1px solid #dcdcdc;border-left:6px solid var(--green);display:flex;align-items:center;justify-content:space-between;padding:0 22px;font-size:15px;color:var(--ink);font-weight:300}
.field{position:absolute;background:var(--white);border:1px solid #ccc;font-size:11.5px;color:#777;padding:0 12px;display:flex;align-items:center}
.foot-head{position:absolute;font-size:15px;font-weight:500;color:var(--ink);text-transform:uppercase}
.foot-links{position:absolute;list-style:none;font-size:12.5px;color:var(--ink);font-weight:300}
.foot-links li{height:29.6px}
</style>
</head>
<body>

<header>
  <div class="brand abs" style="left:74px;top:14px;font-size:28px">Garvel Pryce<br>Transport</div>
  <div class="abs" style="left:707px;top:29px;width:36px;height:36px;border:2px solid var(--green);display:flex;align-items:center;justify-content:center">
    <svg width="18" height="18" viewBox="0 0 24 24"><path d="M6.6 10.8a15 15 0 0 0 6.6 6.6l2.2-2.2c.3-.3.7-.4 1-.2 1.1.4 2.3.6 3.6.6.6 0 1 .4 1 1V20c0 .6-.4 1-1 1A17 17 0 0 1 3 4c0-.6.4-1 1-1h3.5c.6 0 1 .4 1 1 0 1.3.2 2.5.6 3.6.1.3 0 .7-.2 1z" fill="var(--green)"/></svg>
  </div>
  <div class="abs" style="left:752px;top:34px;font-size:21px;color:var(--ink)">+1 555-014-2200</div>
  <div class="btn" style="left:933px;top:29px;width:193px;height:37px">Request a quote</div>
</header>

<section>
  <div class="photo" role="img" aria-label="Refrigerated articulated lorry driving along a coastal road under a cloudy sky" style="left:0;top:91px;width:1200px;height:661px;background:linear-gradient(180deg,#7f94a6 0%,#a8b6c0 30%,#8e9690 52%,#4a4f52 70%,#34383a 100%)"></div>
  <nav class="nav abs" style="left:0;top:91px;width:1200px;height:64px;background:rgba(55,62,70,.72);display:flex;justify-content:center;align-items:center;gap:50px">
    <a style="border-bottom:2px solid var(--white);padding-bottom:6px;margin-top:8px">Home</a>
    <a>About Us</a><a>Services</a><a>Testimonials</a><a>Blog</a><a>FAQ's</a><a>Contact Us</a>
  </nav>
  <h1 class="abs" style="left:68px;top:275px;font-family:'Open Sans',sans-serif;font-weight:700;font-size:82px;line-height:66px;color:var(--white)">Garvel Pryce<br>Transport</h1>
  <div class="abs" style="left:76px;top:446px;font-size:29px;color:var(--white)">We are a Haulage company.</div>
  <div class="btn" style="left:74px;top:510px;width:151px;height:43px">Read more</div>
  <div class="abs" style="left:554px;top:692px;display:flex;gap:14px">
    <span style="width:14px;height:14px;border-radius:50%;background:var(--red)"></span>
    <span style="width:14px;height:14px;border-radius:50%;background:var(--white)"></span>
    <span style="width:14px;height:14px;border-radius:50%;background:var(--white)"></span>
    <span style="width:14px;height:14px;border-radius:50%;background:var(--white)"></span>
  </div>
</section>

<section>
  <div class="abs" style="left:61px;top:906px;width:436px;height:318px;background:var(--green)"></div>
  <div class="photo" role="img" aria-label="Two white and maroon lorry cabs parked side by side" style="left:74px;top:831px;width:512px;height:379px;background:linear-gradient(180deg,#c9d3da 0%,#b8c1c6 45%,#6f7b5c 60%,#9a9c98 100%)"></div>
  <h2 class="section-title" style="left:615px;top:868px;font-size:31px">About Garvel Pryce Transport</h2>
  <div class="underline" style="left:615px;top:919px"></div>
  <p class="para" style="left:615px;top:939px;width:510px">Sed ut perspiciatis unde omnis iste natus error sit voluptatem accusantium doloremque laudantium, totam rem aperiam, eaque ipsa quae ab illo inventore veritatis et quasi architecto beatae vitae dicta sunt explicabo. Nemo enim ipsam voluptatem quia voluptas sit aspernatur aut odit aut fugit, sed quia consequuntur magni dolores eos qui ratione voluptatem sequi nesciunt.</p>
  <div class="btn" style="left:615px;top:1120px;width:151px;height:44px">Read more</div>
</section>

<section>
  <div class="abs" style="left:0;top:1313px;width:1200px;height:678px;background:var(--soft)"></div>
  <h2 class="section-title" style="left:74px;top:1385px">Our Services</h2>
  <div class="underline" style="left:74px;top:1435px"></div>
  <div class="arrows" style="left:1062px;top:1394px">
    <svg width="22" height="22" viewBox="0 0 22 22"><circle cx="11" cy="11" r="11" fill="#c8c8c8"/><path d="M16 11H7m4-4-4 4 4 4" stroke="#fff" stroke-width="2.2" fill="none"/></svg>
    <svg width="22" height="22" viewBox="0 0 22 22"><circle cx="11" cy="11" r="11" fill="var(--red)"/><path d="M6 11h9m-4-4 4 4-4 4" stroke="#fff" stroke-width="2.2" fill="none"/></svg>
  </div>

  <div class="photo" role="img" aria-label="White lorry with maroon cab on a wet yard" style="left:74px;top:1470px;width:330px;height:237px;background:linear-gradient(180deg,#9fb3c4,#d8dcde 55%,#7b7f82)"></div>
  <div class="card-head" style="left:74px;top:1725px">Excepteur sint occaecat</div>
  <p class="para" style="left:74px;top:1754px;width:330px;line-height:24px">Natus error sit voluptatem accusantium doloremque laudantium, totam aute irure dolor in reprehenderit in voluptate velit esse cillum dolore eu fugiat.</p>
  <div class="btn" style="left:74px;top:1872px;width:135px;height:39px">Read more</div>

  <div class="photo" role="img" aria-label="Smiling lorry driver in a cap standing beside his truck" style="left:436px;top:1470px;width:330px;height:237px;background:linear-gradient(135deg,#d4d6d7,#8a8d90 55%,#2c2e30)"></div>
  <div class="card-head" style="left:436px;top:1725px">Excepteur sint occaecat</div>
  <p class="para" style="left:436px;top:1754px;width:330px;line-height:24px">Natus error sit voluptatem accusantium doloremque laudantium, totam aute irure dolor in reprehenderit in voluptate velit esse cillum dolore eu fugiat.</p>
  <div class="btn" style="left:436px;top:1872px;width:135px;height:39px">Read more</div>

  <div class="photo" role="img" aria-label="Row of red lorries parked at a warehouse loading bay" style="left:798px;top:1470px;width:330px;height:237px;background:linear-gradient(180deg,#7fa3c4,#c4a98a 40%,#b23a2c 62%,#5c6670)"></div>
  <div class="card-head" style="left:798px;top:1725px">Excepteur sint occaecat</div>
  <p class="para" style="left:798px;top:1754px;width:330px;line-height:24px">Natus error sit voluptatem accusantium doloremque laudantium, totam aute irure dolor in reprehenderit in voluptate velit esse cillum dolore eu fugiat.</p>
  <div class="btn" style="left:798px;top:1872px;width:135px;height:39px">Read more</div>
</section>

<section>
  <h2 class="section-title" style="left:74px;top:2067px">Client Testimonials</h2>
  <div class="underline" style="left:74px;top:2117px"></div>
  <div class="arrows" style="left:1062px;top:2076px">
    <svg width="22" height="22" viewBox="0 0 22 22"><circle cx="11" cy="11" r="11" fill="#c8c8c8"/><path d="M16 11H7m4-4-4 4 4 4" stroke="#fff" stroke-width="2.2" fill="none"/></svg>
    <svg width="22" height="22" viewBox="0 0 22 22"><circle cx="11" cy="11" r="11" fill="var(--red)"/><path d="M6 11h9m-4-4 4 4-4 4" stroke="#fff" stroke-width="2.2" fill="none"/></svg>
  </div>
  <svg width="0" height="0" style="position:absolute"><defs><symbol id="star" viewBox="0 0 20 20"><polygon points="10,1 12.6,7 19,7.5 14,11.8 15.6,18.5 10,15 4.4,18.5 6,11.8 1,7.5 7.4,7" fill="var(--star)"/></symbol></defs></svg>

  <div class="abs" style="left:74px;top:2168px;display:flex;gap:4px"><svg width="14" height="14"><use href="#star"/></svg><svg width="14" height="14"><use href="#star"/></svg><svg width="14" height="14"><use href="#star"/></svg><svg width="14" height="14"><use href="#star"/></svg><svg width="14" height="14"><use href="#star"/></svg></div>
  <p class="para" style="left:74px;top:2188px;width:330px;font-style:italic;font-size:13px;line-height:24px">" Natus error sit voluptatem accusantium doloremque laudantium, totam rem aperiam, eaque ipsa quae ab illo inventore.."</p>
  <div class="photo" role="img" aria-label="Client portrait" style="left:74px;top:2281px;width:44px;height:44px;border-radius:50%;background:linear-gradient(135deg,#c9cdd1,#5a6068)"></div>
  <div class="abs" style="left:131px;top:2285px;font-size:14px;font-weight:500;color:var(--red)">NAME HEADING</div>
  <div class="abs" style="left:131px;top:2306px;font-size:12px;color:var(--green);font-weight:300">Location</div>

  <div class="abs" style="left:436px;top:2168px;display:flex;gap:4px"><svg width="14" height="14"><use href="#star"/></svg><svg width="14" height="14"><use href="#star"/></svg><svg width="14" height="14"><use href="#star"/></svg><svg width="14" height="14"><use href="#star"/></svg><svg width="14" height="14"><use href="#star"/></svg></div>
  <p class="para" style="left:436px;top:2188px;width:330px;font-style:italic;font-size:13px;line-height:24px">" Natus error sit voluptatem accusantium doloremque laudantium, totam rem aperiam, eaque ipsa quae ab illo inventore.."</p>
  <div class="photo" role="img" aria-label="Client portrait" style="left:436px;top:2281px;width:44px;height:44px;border-radius:50%;background:linear-gradient(135deg,#c9cdd1,#5a6068)"></div>
  <div class="abs" style="left:493px;top:2285px;font-size:14px;font-weight:500;color:var(--red)">NAME HEADING</div>
  <div class="abs" style="left:493px;top:2306px;font-size:12px;color:var(--green);font-weight:300">Location</div>

  <div class="abs" style="left:798px;top:2168px;display:flex;gap:4px"><svg width="14" height="14"><use href="#star"/></svg><svg width="14" height="14"><use href="#star"/></svg><svg width="14" height="14"><use href="#star"/></svg><svg width="14" height="14"><use href="#star"/></svg><svg width="14" height="14"><use href="#star"/></svg></div>
  <p class="para" style="left:798px;top:2188px;width:330px;font-style:italic;font-size:13px;line-height:24px">" Natus error sit voluptatem accusantium doloremque laudantium, totam rem aperiam, eaque ipsa quae ab illo inventore.."</p>
  <div class="photo" role="img" aria-label="Client portrait" style="left:798px;top:2281px;width:44px;height:44px;border-radius:50%;background:linear-gradient(135deg,#c9cdd1,#5a6068)"></div>
  <div class="abs" style="left:855px;top:2285px;font-size:14px;font-weight:500;color:var(--red)">NAME HEADING</div>
  <div class="abs" style="left:855px;top:2306px;font-size:12px;color:var(--green);font-weight:300">Location</div>
</section>

<section>
  <div class="abs" style="left:0;top:2396px;width:1200px;height:511px;background:var(--soft)"></div>
  <h2 class="section-title" style="left:0;width:1200px;text-align:center;top:2473px">Frequently Asked Questions</h2>
  <div class="underline" style="left:545px;top:2523px"></div>
  <div class="faq" style="left:74px;top:2564px">Neque porro quisquam est,qui dolorem? <span style="color:var(--red)">›</span></div>
  <div class="faq" style="left:74px;top:2632px">Neque porro quisquam est,qui dolorem? <span style="color:var(--red)">›</span></div>
  <div class="faq" style="left:74px;top:2700px">Neque porro quisquam est,qui dolorem? <span style="color:var(--red)">›</span></div>
  <div class="faq" style="left:74px;top:2768px">Neque porro quisquam est,qui dolorem? <span style="color:var(--red)">›</span></div>
  <div class="faq" style="left:613px;top:2564px">Neque porro quisquam est,qui dolorem? <span style="color:var(--red)">›</span></div>
  <div class="faq" style="left:613px;top:2632px">Neque porro quisquam est,qui dolorem? <span style="color:var(--red)">›</span></div>
  <div class="faq" style="left:613px;top:2700px">Neque porro quisquam est,qui dolorem? <span style="color:var(--red)">›</span></div>
  <div class="faq" style="left:613px;top:2768px">Neque porro quisquam est,qui dolorem? <span style="color:var(--red)">›</span></div>
</section>

<section>
  <h2 class="section-title" style="left:74px;top:2953px">Blog Posts</h2>
  <div class="underline" style="left:74px;top:3003px"></div>
  <div class="arrows" style="left:1062px;top:2962px">
    <svg width="22" height="22" viewBox="0 0 22 22"><circle cx="11" cy="11" r="11" fill="#c8c8c8"/><path d="M16 11H7m4-4-4 4 4 4" stroke="#fff" stroke-width="2.2" fill="none"/></svg>
    <svg width="22" height="22" viewBox="0 0 22 22"><circle cx="11" cy="11" r="11" fill="var(--red)"/><path d="M6 11h9m-4-4 4 4-4 4" stroke="#fff" stroke-width="2.2" fill="none"/></svg>
  </div>

  <div class="photo" role="img" aria-label="Lorry on a mountain highway" style="left:74px;top:3039px;width:330px;height:236px;background:linear-gradient(180deg,#9ec1dc,#7c9a7a 50%,#5d6468)"></div>
  <div class="abs" style="left:74px;top:3250px;width:308px;height:40px;background:var(--white)"></div>
  <div class="abs" style="left:74px;top:3258px;font-size:11px;color:var(--green)">JUN, 04, 2024</div>
  <div class="abs" style="left:74px;top:3278px;font-size:19px;font-weight:500;color:var(--ink)">SED UT PERSPICIATIS UNDE</div>
  <p class="para" style="left:74px;top:3307px;width:330px;font-size:13px;line-height:24px">Natus error sit voluptatem accusantium doloremque laudantium, totam rem aperiam, eaque ipsa quae ab illo inventore..</p>
  <div class="abs" style="left:74px;top:3393px;font-size:14px;font-weight:500;color:var(--red)">Read More</div>

  <div class="photo" role="img" aria-label="Lorries parked at night" style="left:436px;top:3039px;width:330px;height:236px;background:linear-gradient(180deg,#2c2a26,#6b6660 55%,#3a3632)"></div>
  <div class="abs" style="left:436px;top:3250px;width:300px;height:40px;background:var(--white)"></div>
  <div class="abs" style="left:436px;top:3258px;font-size:11px;color:var(--green)">JUN, 04, 2024</div>
  <div class="abs" style="left:436px;top:3278px;font-size:19px;font-weight:500;color:var(--ink)">SED UT PERSPICIATIS UNDE</div>
  <p class="para" style="left:436px;top:3307px;width:330px;font-size:13px;line-height:24px">Natus error sit voluptatem accusantium doloremque laudantium, totam rem aperiam, eaque ipsa quae ab illo inventore..</p>
  <div class="abs" style="left:436px;top:3393px;font-size:14px;font-weight:500;color:var(--red)">Read More</div>

  <div class="photo" role="img" aria-label="Vans and a box truck at a warehouse dock" style="left:798px;top:3039px;width:330px;height:236px;background:linear-gradient(180deg,#8fb6d8,#dcdad4 40%,#3d5f95 65%,#9c9a96)"></div>
  <div class="abs" style="left:798px;top:3250px;width:300px;height:40px;background:var(--white)"></div>
  <div class="abs" style="left:798px;top:3258px;font-size:11px;color:var(--green)">JUN, 04, 2024</div>
  <div class="abs" style="left:798px;top:3278px;font-size:19px;font-weight:500;color:var(--ink)">SED UT PERSPICIATIS UNDE</div>
  <p class="para" style="left:798px;top:3307px;width:330px;font-size:13px;line-height:24px">Natus error sit voluptatem accusantium doloremque laudantium, totam rem aperiam, eaque ipsa quae ab illo inventore..</p>
  <div class="abs" style="left:798px;top:3393px;font-size:14px;font-weight:500;color:var(--red)">Read More</div>
</section>

<section>
  <div class="photo" role="img" aria-label="Red-toned lorry background" style="left:0;top:3490px;width:1200px;height:515px;background:linear-gradient(180deg,#b3161a 0%,#3a0507 45%,#2a0304 60%,#a11417 100%)"></div>
  <h2 class="abs" style="left:75px;top:3550px;font-size:31px;font-weight:500;color:var(--white)">CONTACT US</h2>
  <div class="abs" style="left:75px;top:3626px;font-size:13.5px;color:var(--white);font-weight:300">Sed ut perspiciatis unde omnis iste natus error sit voluptatem.</div>
  <div class="field" style="left:74px;top:3664px;width:249px;height:42px">Name</div>
  <div class="field" style="left:336px;top:3664px;width:249px;height:42px">Email Address</div>
  <div class="field" style="left:74px;top:3721px;width:249px;height:43px">Phone No</div>
  <div class="field" style="left:336px;top:3721px;width:249px;height:43px">Subject</div>
  <div class="field" style="left:74px;top:3780px;width:511px;height:93px;align-items:flex-start;padding-top:14px">Message</div>
  <div class="btn" style="left:74px;top:3892px;width:151px;height:41px;background:var(--green)">Submit</div>
  <div class="abs" style="left:706px;top:3628px;width:435px;height:323px;background:var(--green)"></div>
  <div class="photo" role="img" aria-label="Smiling driver holding a phone beside his lorry" style="left:613px;top:3559px;width:513px;height:379px;background:linear-gradient(120deg,#6c737a,#b6b8b6 45%,#6a2a22 75%,#2a2c30)"></div>
</section>

<footer>
  <div class="brand abs" style="left:74px;top:4126px;font-size:27px">Garvel Pryce<br>Transport</div>
  <div class="abs" style="left:75px;top:4210px;font-size:12px;line-height:20px;color:var(--ink);font-weight:300">Copyright © 2024 Garvel Pryce Transport.<br>All Rights Reserved</div>

  <div class="foot-head" style="left:356px;top:4063px">Site Map</div>
  <ul class="foot-links" style="left:356px;top:4095px">
    <li>Home</li><li>About Us</li><li>Services</li><li>Testimonials</li><li>Blog</li><li>FAQ's</li><li>Contact Us</li>
  </ul>

  <div class="foot-head" style="left:580px;top:4063px">Contact Info</div>
  <svg class="abs" style="left:580px;top:4099px" width="15" height="13" viewBox="0 0 15 13"><path d="M1 2l4-1.5 5 1.5 4-1.5v10.5l-4 1.5-5-1.5-4 1.5z" fill="var(--green)"/></svg>
  <div class="abs" style="left:609px;top:4095px;font-size:12.5px;line-height:25px;color:var(--ink);font-weight:300">48 Harlow Wharf Rd, Unit 12,<br>Newark 07105, United States</div>
  <svg class="abs" style="left:580px;top:4152px" width="13" height="13" viewBox="0 0 24 24"><path d="M6.6 10.8a15 15 0 0 0 6.6 6.6l2.2-2.2c.3-.3.7-.4 1-.2 1.1.4 2.3.6 3.6.6.6 0 1 .4 1 1V20c0 .6-.4 1-1 1A17 17 0 0 1 3 4c0-.6.4-1 1-1h3.5c.6 0 1 .4 1 1 0 1.3.2 2.5.6 3.6.1.3 0 .7-.2 1z" fill="var(--green)"/></svg>
  <div class="abs" style="left:609px;top:4149px;font-size:12.5px;color:var(--ink);font-weight:300">+1 555-014-2200</div>
  <svg class="abs" style="left:580px;top:4182px" width="14" height="11" viewBox="0 0 14 11"><rect width="14" height="11" rx="1" fill="var(--green)"/><path d="M1 1l6 5 6-5" stroke="#fff" stroke-width="1.3" fill="none"/></svg>
  <div class="abs" style="left:609px;top:4178px;font-size:12.5px;color:var(--ink);font-weight:300">hello@garvelpryce.com</div>
  <div class="abs" style="left:580px;top:4232px;display:flex;gap:16px">
    <span style="width:22px;height:22px;border-radius:50%;background:var(--red)"></span>
    <span style="width:22px;height:22px;border-radius:50%;background:var(--red)"></span>
    <span style="width:22px;height:22px;border-radius:50%;background:var(--red)"></span>
    <span style="width:22px;height:22px;border-radius:50%;background:var(--red)"></span>
    <span style="width:22px;height:22px;border-radius:50%;background:var(--red)"></span>
  </div>

  <div class="foot-head" style="left:884px;top:4063px">Newsletter</div>
  <div class="abs" style="left:884px;top:4095px;font-size:12.5px;line-height:24px;color:var(--ink);font-weight:300;width:240px">Sed ut perspiciatis unde omnis iste natus error sit.</div>
  <div class="field" style="left:884px;top:4157px;width:242px;height:43px;border-color:#999;justify-content:space-between;font-size:12px;color:#444">Enter Email
    <svg width="15" height="15" viewBox="0 0 22 22"><circle cx="11" cy="11" r="11" fill="var(--green)"/><path d="M6 11h9m-4-4 4 4-4 4" stroke="#fff" stroke-width="2.4" fill="none"/></svg>
  </div>
</footer>

</body>
</html>
```